Brightmoor Talent company

We require a website for job recruitment company called "Brightmoor Talent"
Our company is specialising in recruitment of skilled labour from Sri Lanka into Australian market.
We would like to include a job advertising plugin where jobs can be listed and applied for .
COPYWRITING MUST BE INCLUDED !

Industry/Entity Type

Recruitment

Coding

Coded - Design and coding required

Number of Pages Required

5+ page

Colors

Designer to choose colors to be used in the design.

```html
<!DOCTYPE html>
<html lang="en">
<head>
<meta charset="utf-8">
<title>Brightmoor Talent — Recruitment News &amp; Jobs</title>
<link rel="stylesheet" href="https://fonts.googleapis.com/css2?family=Open+Sans:ital,wght@0,400;0,600;0,700;1,400&family=Roboto:wght@400;700&family=Oswald:wght@400&display=swap">
<style>
  :root {
    --slate: #878d99;
    --white: #ffffff;
    --ink: #111111;
    --accent: #db545a;
    --dark: #333333;
    --link: #c9d6ea;
    --brand: #4d4d4d;
  }
  * { box-sizing: border-box; margin: 0; padding: 0; }
  html, body { width: 1200px; height: 2294px; overflow: hidden; }
  body { position: relative; font-family: "Open Sans", sans-serif; color: var(--ink); background: var(--white); }
  .abs { position: absolute; }
  h1, h2, h3 { font-weight: 400; }

  .site-header { left: 0; top: 0; width: 1200px; height: 63px; background: var(--white); }
  .brand { left: 83px; top: 14px; font-weight: 700; font-size: 24px; color: var(--brand); white-space: nowrap; }
  .nav { top: 21px; font-weight: 600; font-size: 15px; color: #555; }

  .latest { left: 0; top: 63px; width: 1200px; height: 797px; background: var(--slate); }
  .section-title { left: 0; width: 1200px; text-align: center; font-family: "Roboto", sans-serif; font-weight: 700; font-size: 44px; color: var(--white); text-shadow: 2px 3px 4px rgba(0,0,0,.35); }
  .rule { left: 555px; top: 192px; width: 90px; height: 2px; background: #444; }
  .feature-card { top: 222px; width: 344px; height: 596px; }
  .feature-card.active { background: var(--white); }
  .feature-photo { left: 27px; top: 27px; width: 290px; height: 297px; }
  .feature-headline { left: 0; top: 358px; width: 344px; text-align: center; font-family: "Roboto", sans-serif; font-size: 22px; color: var(--white); white-space: nowrap; }
  .feature-text { left: 20px; top: 404px; width: 304px; text-align: center; font-size: 15px; line-height: 22px; color: var(--white); }
  .feature-date { left: 0; top: 470px; width: 344px; text-align: center; font-size: 15px; color: var(--accent); }
  .active .feature-headline, .active .feature-text { color: var(--ink); }
  .btn-read { left: 107px; top: 510px; width: 129px; height: 41px; background: var(--accent); color: var(--white); font-size: 15px; line-height: 41px; text-align: center; }

  .posts { left: 0; top: 860px; width: 1200px; height: 683px; background: linear-gradient(to bottom, var(--slate) 0%, #c3c6cc 55%, var(--white) 100%); }
  .posts-heading { left: 0; top: 935px; width: 1200px; text-align: center; font-family: "Oswald", sans-serif; font-size: 45px; color: var(--white); }
  .post-card { top: 1034px; width: 331px; height: 370px; background: var(--white); }
  .post-photo { left: 0; top: 0; width: 331px; height: 201px; }
  .post-headline { left: 0; top: 214px; width: 331px; text-align: center; font-family: "Roboto", sans-serif; font-size: 22px; white-space: nowrap; }
  .post-text { left: 20px; top: 260px; width: 291px; text-align: center; font-size: 15px; line-height: 22px; }
  .post-more { left: 0; top: 320px; width: 331px; text-align: center; font-size: 15px; letter-spacing: 1.5px; }
  .btn-learn { left: 521px; top: 1431px; width: 158px; height: 44px; border: 2px solid var(--white); color: var(--white); font-size: 14px; letter-spacing: 1px; line-height: 40px; text-align: center; }

  .faq-section { left: 0; top: 1543px; width: 1200px; height: 586px; background: var(--slate); }
  .faq-intro { left: 0; top: 1662px; width: 1200px; text-align: center; font-style: italic; font-size: 15px; color: var(--white); letter-spacing: -.3px; }
  .faq-item { left: 83px; width: 1033px; background: var(--white); }
  .faq-q { left: 27px; top: 21px; font-weight: 700; font-size: 15px; }
  .faq-plus { right: 27px; top: 22px; width: 16px; height: 16px; }
  .faq-a { left: 27px; top: 98px; width: 985px; font-size: 15px; line-height: 23px; }

  .site-footer { left: 0; top: 2129px; width: 1200px; height: 76px; background: var(--white); }
  .footer-brand { left: 83px; top: 2147px; font-weight: 700; font-size: 28px; color: var(--brand); }
  .social { top: 2137px; width: 51px; height: 51px; border-radius: 50%; }
  .credit-bar { left: 0; top: 2205px; width: 1200px; height: 89px; background: var(--dark); }
  .credit { left: 0; top: 2241px; width: 1200px; text-align: center; font-size: 12px; color: var(--white); }
  .credit span { color: var(--link); text-decoration: underline; }
</style>
</head>
<body>
  <header class="abs site-header">
    <div class="abs brand">Brightmoor Talent</div>
    <nav>
      <span class="abs nav" style="left:763px">Home</span>
      <span class="abs nav" style="left:842px">work</span>
      <span class="abs nav" style="left:915px">About us</span>
      <span class="abs nav" style="left:1016px">Contact us</span>
    </nav>
  </header>

  <section class="abs latest"></section>
  <h1 class="abs section-title" style="top:112px">Latest Blog</h1>
  <div class="abs rule"></div>

  <article class="abs feature-card" style="left:83px">
    <div class="abs feature-photo" role="img" aria-label="Employer and new recruit shaking hands in a bright office" style="background:linear-gradient(160deg,#f1eeea,#d8cfc8 55%,#3a3f4c)"></div>
    <h3 class="abs feature-headline">Welders Wanted in Perth</h3>
    <p class="abs feature-text">Twelve skilled welding roles now open for Sri Lankan tradespeople.</p>
    <p class="abs feature-date">Thu Nov 17 2022</p>
    <div class="abs btn-read">Apply Now</div>
  </article>
  <article class="abs feature-card active" style="left:428px">
    <div class="abs feature-photo" role="img" aria-label="Candidate signing an employment contract beside a laptop" style="background:linear-gradient(160deg,#ece8df,#e6e9ec 60%,#b9b2ab)"></div>
    <h3 class="abs feature-headline">Your Visa, Step by Step</h3>
    <p class="abs feature-text">How we guide skilled workers through the Australian visa process.</p>
    <p class="abs feature-date">Thu Nov 17 2022</p>
    <div class="abs btn-read">Read More</div>
  </article>
  <article class="abs feature-card" style="left:772px">
    <div class="abs feature-photo" role="img" aria-label="Laptop, phone and notebook on a wooden desk" style="background:linear-gradient(150deg,#5c5a55,#8a7058 50%,#d9d3c4)"></div>
    <h3 class="abs feature-headline">Hiring from Sri Lanka</h3>
    <p class="abs feature-text">Australian employers: fill skill gaps with trusted, vetted talent.</p>
    <p class="abs feature-date">Thu Nov 17 2022</p>
    <div class="abs btn-read">Read More</div>
  </article>

  <section class="abs posts"></section>
  <h2 class="abs posts-heading">Blog Posts</h2>

  <article class="abs post-card" style="left:83px">
    <div class="abs post-photo" role="img" aria-label="Employer and new recruit shaking hands in a bright office" style="background:linear-gradient(160deg,#f1eeea,#d8cfc8 55%,#3a3f4c)"></div>
    <h3 class="abs post-headline">Electricians for Brisbane</h3>
    <p class="abs post-text">Licensed electricians needed for major projects. Relocation support.</p>
    <p class="abs post-more">VIEW JOB</p>
  </article>
  <article class="abs post-card" style="left:434px">
    <div class="abs post-photo" role="img" aria-label="Candidate signing an employment contract beside a laptop" style="background:linear-gradient(160deg,#ece8df,#e6e9ec 60%,#b9b2ab)"></div>
    <h3 class="abs post-headline">Aged Care Nurses, Sydney</h3>
    <p class="abs post-text">Registered nurses wanted. Sponsorship and housing help included.</p>
    <p class="abs post-more">VIEW JOB</p>
  </article>
  <article class="abs post-card" style="left:786px">
    <div class="abs post-photo" role="img" aria-label="Laptop, phone and notebook on a wooden desk" style="background:linear-gradient(150deg,#5c5a55,#8a7058 50%,#d9d3c4)"></div>
    <h3 class="abs post-headline">Chefs for Melbourne</h3>
    <p class="abs post-text">Experienced cooks and chefs for busy hotels and restaurants.</p>
    <p class="abs post-more">VIEW JOB</p>
  </article>
  <div class="abs btn-learn">ALL JOBS</div>

  <section class="abs faq-section"></section>
  <h2 class="abs section-title" style="top:1594px">Facts &amp; Questions</h2>
  <p class="abs faq-intro">Answers for skilled workers in Sri Lanka and employers across Australia looking to hire.</p>

  <div class="abs faq-item" style="top:1713px;height:208px">
    <p class="abs faq-q">Do you help with my visa?</p>
    <svg class="abs faq-plus" viewBox="0 0 16 16"><path d="M8 0v16M0 8h16" stroke="#111" stroke-width="2"/></svg>
    <p class="abs faq-a">Yes. Once an Australian employer offers you a role, our team works with registered migration agents to prepare your skills assessment, English test plan and sponsored visa application. We keep you updated at every step, help you arrange flights and first accommodation, and stay in touch after you arrive so your move is smooth.</p>
  </div>
  <div class="abs faq-item" style="top:1932px;height:66px">
    <p class="abs faq-q">Which trades are in demand?</p>
    <svg class="abs faq-plus" viewBox="0 0 16 16"><path d="M8 0v16M0 8h16" stroke="#111" stroke-width="2"/></svg>
  </div>
  <div class="abs faq-item" style="top:2009px;height:66px">
    <p class="abs faq-q">How do I apply for a job?</p>
    <svg class="abs faq-plus" viewBox="0 0 16 16"><path d="M8 0v16M0 8h16" stroke="#111" stroke-width="2"/></svg>
  </div>

  <footer class="abs site-footer"></footer>
  <div class="abs footer-brand">Brightmoor Talent</div>
  <div class="abs social" style="left:932px;background:#2c4a8c" role="img" aria-label="Social profile link"></div>
  <div class="abs social" style="left:992px;background:#3da3e0" role="img" aria-label="Social profile link"></div>
  <div class="abs social" style="left:1052px;background:#c2349a" role="img" aria-label="Social profile link"></div>
  <div class="abs credit-bar"></div>
  <p class="abs credit"><span>Job Listings</span> updated daily by <span>Brightmoor Talent</span>.</p>
</body>
</html>
```